A clean crisp business card for a Landscape Construction company. Designed to be easy to read contact/ info and also be appealing/interesting, unlike a traditional business card.

Industry/Entity Type

Landscape Construction

Contact Information for Business Card

Company name : Brambleford Landscape Construction, phone number: (877) 62Vista, website:Bramblefordyards.example, Email, sales@bramblefordyards.example

Requirements
Nice to have
• Luxurious finishes/ details…. Icons or emblems next to contact info
Should not have
• Clipart or general pictures

```html
<!DOCTYPE html>
<html lang="en">
<head>
<meta charset="utf-8">
<title>Brambleford Landscape Construction – Business Card</title>
<link rel="stylesheet" href="https://fonts.googleapis.com/css2?family=Marcellus&family=Arimo:wght@400&display=swap">
<style>
  :root {
    --backdrop: #3a302c;
    --card-black: #161616;
    --card-white: #ffffff;
    --leaf-green: #97c93d;
    --brand-blue: #1f6fcf;
    --ink: #1a1a1a;
  }
  * { margin: 0; padding: 0; box-sizing: border-box; }
  html, body { width: 1200px; height: 716px; overflow: hidden; }
  body {
    background: var(--backdrop);
    position: relative;
    font-family: "Arimo", Arial, sans-serif;
  }
  .card {
    position: absolute;
    top: 203px;
    width: 540px;
    height: 310px;
    border-bottom: 3px solid var(--leaf-green);
    border-left: 2px solid var(--leaf-green);
    overflow: hidden;
  }
  .card-back { left: 40px; background: var(--card-black); }
  .card-front { left: 620px; background: var(--card-black); }

  .brand-lockup {
    position: absolute;
    display: flex;
    align-items: center;
    gap: 12px;
  }
  .card-back .brand-lockup { left: 0; right: 0; top: 112px; justify-content: center; }
  .card-front .brand-lockup { left: 34px; top: 30px; }
  .brand-dot {
    width: 30px; height: 30px;
    border-radius: 50%;
    background: var(--brand-blue);
    flex: none;
  }
  .brand-name {
    font-family: "Marcellus", serif;
    color: var(--leaf-green);
    font-size: 30px;
    line-height: 1.05;
    letter-spacing: 1px;
  }
  .brand-name small { display: block; font-size: 13px; letter-spacing: 3px; text-transform: uppercase; }
  .card-front .brand-name { font-size: 26px; }

  .card-waves { position: absolute; inset: 0; }

  .holder {
    position: absolute;
    right: 30px;
    top: 206px;
    text-align: right;
    font-family: "Marcellus", serif;
    line-height: 1.1;
  }
  .holder-name { color: var(--brand-blue); font-size: 20px; letter-spacing: 2px; text-transform: uppercase; }
  .holder-role { color: var(--leaf-green); font-size: 13px; letter-spacing: 2px; text-transform: uppercase; margin-top: 2px; }

  .contact-list {
    position: absolute;
    right: 30px;
    top: 250px;
    list-style: none;
    color: var(--ink);
    font-size: 12.5px;
    line-height: 17px;
    text-align: right;
  }
  .contact-list li { display: flex; justify-content: flex-end; align-items: center; gap: 7px; }
  .contact-icon { width: 11px; height: 11px; flex: none; }
</style>
</head>
<body>

  <section class="card card-back" aria-label="Business card back">
    <div class="brand-lockup">
      <span class="brand-dot"></span>
      <span class="brand-name">Brambleford<small>Landscape Construction</small></span>
    </div>
  </section>

  <section class="card card-front" aria-label="Business card front">
    <svg class="card-waves" viewBox="0 0 540 310" aria-hidden="true">
      <path fill="#97c93d" d="M0,70 C20,150 110,196 270,196 C380,196 450,162 540,178 L540,310 L0,310 Z"/>
      <path fill="#1f6fcf" d="M60,100 C110,170 190,178 290,172 C390,166 460,138 540,150 L540,166 C460,156 390,184 290,188 C180,192 100,170 60,100 Z"/>
      <path fill="#ffffff" d="M0,108 C40,175 140,205 280,203 C390,201 460,178 540,186 L540,310 L0,310 Z"/>
    </svg>

    <div class="brand-lockup">
      <span class="brand-dot"></span>
      <span class="brand-name">Brambleford<small>Landscape Construction</small></span>
    </div>

    <div class="holder">
      <p class="holder-name">Daniel Hartley</p>
      <p class="holder-role">Director</p>
    </div>

    <ul class="contact-list">
      <li>(877) 62Vista
        <svg class="contact-icon" viewBox="0 0 12 12" aria-hidden="true"><path fill="#1f6fcf" d="M2.5,0.5 L4.5,0.5 L5,3.5 L3.8,4.5 C4.5,6 6,7.5 7.5,8.2 L8.5,7 L11.5,7.5 L11.5,9.5 C11.5,10.8 10.5,11.5 9.5,11.5 C5,11 1,7 0.5,2.5 C0.5,1.5 1.2,0.5 2.5,0.5 Z"/></svg>
      </li>
      <li>sales@bramblefordyards.example
        <svg class="contact-icon" viewBox="0 0 12 12" aria-hidden="true"><rect x="0.8" y="2.3" width="10.4" height="7.4" rx="1" fill="none" stroke="#1f6fcf" stroke-width="1.3"/><path d="M1,2.8 L6,6.6 L11,2.8" fill="none" stroke="#1f6fcf" stroke-width="1.3"/></svg>
      </li>
      <li>www.bramblefordyards.example
        <svg class="contact-icon" viewBox="0 0 12 12" aria-hidden="true"><circle cx="6" cy="6" r="5.2" fill="none" stroke="#1f6fcf" stroke-width="1.2"/><ellipse cx="6" cy="6" rx="2.2" ry="5.2" fill="none" stroke="#1f6fcf" stroke-width="1"/><path d="M0.8,6 H11.2" stroke="#1f6fcf" stroke-width="1"/></svg>
      </li>
    </ul>
  </section>

</body>
</html>
```